Square V Dental Appointment Cards

This is a sister company of Tamarind Dental Group
We are a returning client.
This is what we like:
We like Parvell
Parvell font is cool
our Client is mostly Hispanic
We like to put Dr. Okafor, WMSU Graduate
Please look at Tamarind Dental Appt. Cards/Business Cards
Updates

We would like to see new logos, too.

Industry/Entity Type

Dental

Contact Information for Business Card

Tobi R. Okafor, D.D.S
WMSU Graduate
2836 West Larkspur Ave., Suite 410
Anaheim, CA 92817

Colors

Designer to choose colors to be used in the design.

Requirements
Nice to have
• Parvell Features

```html
<!DOCTYPE html>
<html lang="en">
<head>
<meta charset="utf-8">
<title>Square V Dental – Appointment Card</title>
<link href="https://fonts.googleapis.com/css2?family=Lato:wght@400;700;900&display=swap" rel="stylesheet">
<style>
  :root {
    --backdrop: #9a9a9a;
    --card: #ffffff;
    --brand-blue: #1c7bb5;
    --brand-orange: #f39a12;
    --ink: #333333;
    --rule: #c9c9c9;
  }
  * { margin: 0; padding: 0; box-sizing: border-box; }
  html, body { width: 1200px; height: 900px; overflow: hidden; }
  body {
    background: var(--backdrop);
    font-family: "Lato", Arial, sans-serif;
    color: var(--ink);
    position: relative;
  }
  .card {
    position: absolute;
    background: var(--card);
    border-radius: 10px;
    overflow: hidden;
    box-shadow: 2px 3px 5px rgba(0,0,0,0.35);
  }
  .card--front { left: 150px; top: 306px; width: 438px; height: 271px; }
  .card--back  { left: 609px; top: 306px; width: 440px; height: 273px; }

  /* front */
  .front-band { position: absolute; left: 0; top: 40px; width: 100%; height: 71px; background: var(--brand-blue); }
  .brand-dot {
    position: absolute; border-radius: 50%; background: var(--card);
  }
  .card--front .brand-dot { left: 170px; top: 28px; width: 98px; height: 98px; }
  .card--front .brand-dot::after {
    content: ""; position: absolute; inset: 12px; border-radius: 50%;
    border: 3px solid var(--brand-orange);
  }
  .wordmark {
    position: absolute; font-weight: 900; text-transform: uppercase; letter-spacing: 1px; white-space: nowrap;
  }
  .card--front .wordmark {
    left: 0; width: 100%; top: 122px; text-align: center; font-size: 22px; color: var(--brand-orange);
  }
  .doctor {
    position: absolute; right: 233px; top: 179px; text-align: right; line-height: 17px;
  }
  .doctor__name { font-size: 14px; font-weight: 700; color: var(--brand-orange); }
  .doctor__title { font-size: 11px; color: var(--brand-blue); }
  .doctor__school { font-size: 13px; }
  .divider { position: absolute; left: 218px; top: 181px; width: 1px; height: 30px; background: var(--brand-blue); }
  .address { position: absolute; left: 232px; top: 180px; font-size: 13px; line-height: 16px; }
  .phone-bar {
    position: absolute; left: 0; bottom: 0; width: 100%; height: 38px; background: var(--brand-orange);
    color: #fff; font-size: 17px; text-align: center; line-height: 36px; letter-spacing: 0.5px;
  }

  /* back */
  .back-band { position: absolute; left: 113px; top: 23px; right: 0; height: 79px; background: var(--brand-orange); }
  .card--back .brand-dot { left: 10px; top: 5px; width: 110px; height: 110px; }
  .card--back .brand-dot::after {
    content: ""; position: absolute; inset: 9px; border-radius: 50%;
    border: 3px solid var(--brand-orange);
  }
  .card--back .wordmark {
    left: 113px; right: 0; top: 49px; text-align: center; font-size: 25px; color: #fff;
  }
  .appointment { position: absolute; left: 32px; top: 130px; font-size: 13px; white-space: nowrap; }
  .weekdays { position: absolute; left: 38px; top: 164px; display: flex; list-style: none; font-size: 13px; }
  .weekdays li { display: flex; align-items: center; margin-right: 15px; }
  .weekdays li:last-child { margin-left: 4px; }
  .checkbox { width: 16px; height: 15px; border: 1px solid #555; margin-right: 6px; }
  .notice { position: absolute; left: 0; width: 100%; top: 194px; text-align: center; font-size: 12.5px; }
  .web-bar {
    position: absolute; left: 0; bottom: 0; width: 100%; height: 49px; background: var(--brand-blue);
    border-top: 2px solid var(--rule);
    color: #fff; font-size: 12px; font-weight: 700; letter-spacing: 1px; text-align: center; line-height: 40px;
  }
</style>
</head>
<body>
  <section class="card card--front" aria-label="Business card front">
    <div class="front-band"></div>
    <div class="brand-dot"></div>
    <p class="wordmark">Square V Dental</p>
    <div class="doctor">
      <p><span class="doctor__name">TOBI R. OKAFOR,</span> <span class="doctor__title">D.D.S</span></p>
      <p class="doctor__school">WMSU Graduate</p>
    </div>
    <div class="divider"></div>
    <address class="address" style="font-style:normal">2836 West Larkspur Ave<br>Suite 410 Anaheim, CA 92817</address>
    <div class="phone-bar">000 222 0000</div>
  </section>

  <section class="card card--back" aria-label="Appointment card back">
    <div class="back-band"></div>
    <div class="brand-dot"></div>
    <p class="wordmark">Square V Dental</p>
    <p class="appointment">YOUR NEXT APPOINTMENT ..................... &nbsp;at................. am/pm</p>
    <ul class="weekdays">
      <li><span class="checkbox"></span>MON</li>
      <li><span class="checkbox"></span>TUE</li>
      <li><span class="checkbox"></span>WED</li>
      <li><span class="checkbox"></span>THU</li>
      <li><span class="checkbox"></span>FRI</li>
      <li><span class="checkbox"></span>SAT</li>
    </ul>
    <p class="notice">If unable to keep appointment, kindly give 24hrs notice.</p>
    <div class="web-bar">www.websitename.com</div>
  </section>
</body>
</html>
```